The Vantor Codex Book Cover

"The Vantor Codex" is a book I wrote with the slogan "Unlock Performance, Spark Engagement: Master the Art of Building Winning Cultures in Today's Hybrid World". The book is designed around a methodology that's mine and that I attached. I would love to see the graphic of the methodology integrated in the design in a very subtle way. Use colors from the model but the book cover should be catchy, modern and engaging to the eye.
Overall the book is about three key elements towards success:
- (Self) Directions (purpose)
- Human experience (people and psychological safety)
- Maximize engagement
The methodology is a FLOW so flow is something that could be incorporated as well in the concept.
Low design quality
Managers and Teams

```html
<!DOCTYPE html>
<html lang="en">
<head>
<meta charset="utf-8">
<title>The Vantor Codex – Book Cover</title>
<link rel="stylesheet" href="https://fonts.googleapis.com/css2?family=Bebas+Neue&family=Fira+Sans+Condensed:wght@400&family=Montserrat:wght@300;500;700&display=swap">
<style>
  :root {
    --backdrop: #dcdde0;
    --cover-dark: #0a1418;
    --cover-grey: #3b3c3f;
    --brand-blue: #27a9e1;
    --ink-white: #ffffff;
    --stud: #9aa3a8;
  }
  html, body {
    margin: 0;
    width: 1200px;
    height: 1200px;
    overflow: hidden;
    background: var(--backdrop);
  }
  .book-cover {
    position: absolute;
    left: 225px;
    top: 36px;
    width: 757px;
    height: 1136px;
    background: var(--cover-dark);
    overflow: hidden;
    box-shadow: 0 2px 6px rgba(0,0,0,0.25);
  }
  .cover-top-glow {
    position: absolute;
    inset: 0 0 auto 0;
    height: 470px;
    background: radial-gradient(ellipse 70% 85% at 25% 20%, #55575b 0%, var(--cover-grey) 35%, var(--cover-dark) 100%);
  }
  .knob-photo {
    position: absolute;
    right: 0;
    top: 0;
    width: 330px;
    height: 390px;
    background: radial-gradient(circle at 62% 48%, #2c3338 0%, #3d8fb8 32%, #1c2a33 48%, #2a2c2f 75%, rgba(42,44,47,0) 100%);
  }
  .cover-art {
    position: absolute;
    inset: 0;
    width: 757px;
    height: 1136px;
  }
  .method-step {
    font-family: "Fira Sans Condensed", sans-serif;
    font-size: 14px;
    fill: var(--ink-white);
  }
  .step-stud { fill: var(--stud); stroke: #e6ecef; stroke-width: 1.2; }
  .flow-arc { fill: none; stroke: var(--brand-blue); stroke-width: 1.2; opacity: 0.8; }
  .title-small, .title-accent, .title-main {
    font-family: "Bebas Neue", sans-serif;
  }
  .title-small { font-size: 89px; fill: var(--ink-white); }
  .title-accent { font-size: 246px; fill: var(--brand-blue); }
  .title-main { font-size: 193px; fill: var(--ink-white); }
  .title-rule { stroke: var(--ink-white); stroke-width: 5; }
  .subtitle-rule { stroke: var(--brand-blue); stroke-width: 1; opacity: 0.8; }
  .subtitle-lead {
    font-family: "Montserrat", sans-serif;
    font-weight: 700;
    font-size: 24px;
    fill: var(--brand-blue);
  }
  .subtitle-line {
    font-family: "Montserrat", sans-serif;
    font-weight: 300;
    font-size: 24px;
    fill: var(--ink-white);
  }
  .author-band { fill: var(--brand-blue); }
  .author-name {
    font-family: "Montserrat", sans-serif;
    font-weight: 500;
    font-size: 42px;
    letter-spacing: 5px;
    fill: var(--ink-white);
  }
</style>
</head>
<body>
  <div class="book-cover">
    <div class="cover-top-glow"></div>
    <div class="knob-photo" role="img" aria-label="Photo of a hand turning a glowing blue control knob marked with gears"></div>

    <svg class="cover-art" viewBox="0 0 757 1136" xmlns="http://www.w3.org/2000/svg">
      <path class="flow-arc" d="M 300 60 C 280 180 330 330 560 380 C 640 395 710 390 757 382"/>

      <g class="method-flow">
        <text class="method-step" x="305" y="43" text-anchor="end">Discover your purpose. Why do you exist?</text>
        <circle class="step-stud" cx="325" cy="38" r="9"/>
        <text class="method-step" x="266" y="82" text-anchor="end">Identify Purpose Activators (Vision)</text>
        <circle class="step-stud" cx="286" cy="77" r="9"/>
        <text class="method-step" x="242" y="115" text-anchor="end">Develop a Master Plan (Strategy)</text>
        <circle class="step-stud" cx="262" cy="110" r="9"/>
        <text class="method-step" x="237" y="144" text-anchor="end">Cultivate Psychological</text>
        <text class="method-step" x="237" y="159" text-anchor="end">Safety and Ownership</text>
        <circle class="step-stud" cx="257" cy="148" r="9"/>
        <text class="method-step" x="252" y="183" text-anchor="end">Tap into People Purpose and</text>
        <text class="method-step" x="252" y="199" text-anchor="end">Passion (Intrinsic Motivation)</text>
        <circle class="step-stud" cx="272" cy="185" r="9"/>
        <text class="method-step" x="268" y="223" text-anchor="end">Unlock culture of personal</text>
        <text class="method-step" x="268" y="237" text-anchor="end">growth &amp; development</text>
        <circle class="step-stud" cx="288" cy="224" r="9"/>
        <text class="method-step" x="304" y="265" text-anchor="end">Prioritize Feedback &amp; Transparency</text>
        <circle class="step-stud" cx="324" cy="260" r="9"/>
        <text class="method-step" x="347" y="302" text-anchor="end">Empower the Community from the bottom-up</text>
        <circle class="step-stud" cx="367" cy="297" r="9"/>
        <text class="method-step" x="396" y="338" text-anchor="end">Put excellent (team) performance in the spotlight</text>
        <circle class="step-stud" cx="416" cy="333" r="9"/>
        <text class="method-step" x="470" y="369" text-anchor="end">Monitor engagement Real-time</text>
        <circle class="step-stud" cx="490" cy="364" r="9"/>
        <text class="method-step" x="539" y="396" text-anchor="end">Reaching full potential of people and organization</text>
        <circle class="step-stud" cx="559" cy="391" r="9"/>
      </g>

      <g class="book-title">
        <line class="title-rule" x1="59" y1="496" x2="316" y2="496"/>
        <line class="title-rule" x1="441" y1="496" x2="698" y2="496"/>
        <text class="title-small" x="378" y="527" text-anchor="middle">THE</text>
        <text class="title-accent" x="59" y="711" textLength="639" lengthAdjust="spacingAndGlyphs">VANTOR</text>
        <text class="title-main" x="59" y="861" textLength="639" lengthAdjust="spacingAndGlyphs">CODEX</text>
      </g>

      <g class="book-subtitle">
        <line class="subtitle-rule" x1="66" y1="905" x2="692" y2="905"/>
        <text class="subtitle-lead" x="66" y="940" textLength="623" lengthAdjust="spacingAndGlyphs">UNLOCK PERFORMANCE, SPARK ENGAGEMENT</text>
        <text class="subtitle-line" x="378" y="972" text-anchor="middle" textLength="540" lengthAdjust="spacingAndGlyphs">MASTER THE ART OF BUILDING WINNING</text>
        <text class="subtitle-line" x="378" y="1003" text-anchor="middle" textLength="510" lengthAdjust="spacingAndGlyphs">CULTURES IN TODAY’S HYBRID WORLD</text>
        <line class="subtitle-rule" x1="66" y1="1013" x2="692" y2="1013"/>
      </g>

      <rect class="author-band" x="0" y="1061" width="757" height="75"/>
      <text class="author-name" x="378" y="1113" text-anchor="middle">AUTHOR NAME</text>
    </svg>
  </div>
</body>
</html>
```